Bram Keystone Homes needs a business card

We need a business card for a new company in Canada, Ontario. Our company is all about luxury contraction homes for our clients. Our product and services are custom projects design. Under the business logo that will be created, we want a slogan that will be a memorable phrase for consumers to remember us to tell their friends and relatives.

Additional infomation
- Ludovic Entrasse
- President / Ceo
-519.604.3087

Find point what luxury construction products and services can be done

We like to see colors:
- #663300
- and something other colors or color that would attract the client needs and wants

The final design should communicate leads from new or old clients that will grow our empire. Most of all, we try to work among the budget that clients want

NOTE
- we also need an icon for the business (Example: Instagram, Facebook, and Whatsapp icons)
- We want the company name to be remembered easily for clients and our distributors who would get our orders.
- we need an icon on the business cards: Facebook and Instagram.

Thanks,
Bram Keystone Homes

```html
<!DOCTYPE html>
<html lang="en">
<head>
<meta charset="utf-8">
<title>Bram Keystone Homes – Business Card</title>
<link rel="stylesheet" href="https://fonts.googleapis.com/css2?family=Roboto+Condensed:wght@500;700&family=Poppins:wght@400;500&display=swap">
<style>
  :root {
    --brand-brown: #663300;
    --ink-grey: #4a4a4a;
    --band-grey: #6b6b6b;
    --card-white: #ffffff;
    --backdrop: #e6e4e1;
  }
  * { margin: 0; padding: 0; box-sizing: border-box; }
  html, body { width: 1200px; height: 874px; overflow: hidden; }
  body {
    background: var(--backdrop);
    display: flex;
    flex-direction: column;
    align-items: center;
    justify-content: center;
    gap: 44px;
  }
  .card {
    position: relative;
    width: 620px;
    height: 354px;
    background: var(--card-white);
    box-shadow: 0 6px 18px rgba(0,0,0,0.12);
    overflow: hidden;
  }
  .wordmark {
    font-family: "Roboto Condensed", Arial, sans-serif;
    font-weight: 700;
    color: var(--brand-brown);
    line-height: 1;
    white-space: nowrap;
  }
  .tagline {
    font-family: "Roboto Condensed", Arial, sans-serif;
    font-weight: 500;
    color: var(--brand-brown);
    text-transform: uppercase;
    white-space: nowrap;
  }

  /* Front */
  .card-front .brand-lockup {
    position: absolute;
    left: 0; right: 0; top: 124px;
    text-align: center;
  }
  .card-front .wordmark { font-size: 48px; }
  .card-front .tagline { font-size: 15px; margin-top: 6px; }
  .contact-icons {
    position: absolute;
    left: 0; right: 0; bottom: 56px;
    display: flex;
    justify-content: center;
    gap: 4px;
  }
  .contact-icons svg { display: block; }

  /* Back */
  .card-back .brand-lockup {
    position: absolute;
    left: 28px; top: 118px;
    width: 300px;
    text-align: center;
  }
  .card-back .wordmark { font-size: 31px; }
  .card-back .tagline { font-size: 10.5px; margin-top: 5px; }
  .divider {
    position: absolute;
    left: 348px; top: 96px;
    width: 2px; height: 128px;
    background: linear-gradient(to bottom, rgba(120,120,120,0), #8a8a8a 40%, #8a8a8a 60%, rgba(120,120,120,0));
  }
  .contact {
    position: absolute;
    left: 372px; top: 128px;
    font-family: "Poppins", Arial, sans-serif;
  }
  .contact-name { font-size: 21px; font-weight: 500; color: var(--brand-brown); }
  .contact-role { font-size: 17px; color: var(--ink-grey); margin-top: 2px; }
  .contact-phone { font-size: 15px; color: var(--ink-grey); margin-top: 2px; }
  .footer-band {
    position: absolute;
    left: 0; right: 0; bottom: 0;
    height: 14px;
    display: flex;
  }
  .footer-band .band-brown { flex: 0 0 60%; background: var(--brand-brown); }
  .footer-band .band-grey { flex: 1; background: var(--band-grey); }
</style>
</head>
<body>
  <section class="card card-front">
    <div class="brand-lockup">
      <div class="wordmark">Bram Keystone Homes</div>
      <div class="tagline">- Home Renovations - Custom Project Design -</div>
    </div>
    <div class="contact-icons" aria-label="Contact icons">
      <svg width="28" height="28" viewBox="0 0 28 28" role="img" aria-label="Email">
        <circle cx="14" cy="14" r="12.5" fill="none" stroke="#663300" stroke-width="1"/>
        <rect x="8" y="10" width="12" height="8.5" rx="1" fill="none" stroke="#663300" stroke-width="1.4"/>
        <path d="M8.5 10.5 L14 15 L19.5 10.5" fill="none" stroke="#663300" stroke-width="1.4"/>
      </svg>
      <svg width="28" height="28" viewBox="0 0 28 28" role="img" aria-label="Location">
        <circle cx="14" cy="14" r="12.5" fill="none" stroke="#663300" stroke-width="1"/>
        <path d="M14 21 C10.5 16.5 9.5 14.5 9.5 12.5 A4.5 4.5 0 0 1 18.5 12.5 C18.5 14.5 17.5 16.5 14 21 Z" fill="#663300"/>
        <circle cx="14" cy="12.5" r="1.7" fill="#ffffff"/>
      </svg>
      <svg width="28" height="28" viewBox="0 0 28 28" role="img" aria-label="Phone">
        <circle cx="14" cy="14" r="12.5" fill="none" stroke="#663300" stroke-width="1"/>
        <path d="M10.2 8.5 L12.2 8.5 L13 11.5 L11.6 12.6 C12.3 14.2 13.8 15.7 15.4 16.4 L16.5 15 L19.5 15.8 L19.5 17.8 C19.5 18.6 18.8 19.3 18 19.2 C12.9 18.8 9.2 15.1 8.8 10 C8.7 9.2 9.4 8.5 10.2 8.5 Z" fill="#663300"/>
      </svg>
    </div>
  </section>

  <section class="card card-back">
    <div class="brand-lockup">
      <div class="wordmark">Bram Keystone Homes</div>
      <div class="tagline">- Home Renovations - Custom Project Design -</div>
    </div>
    <div class="divider"></div>
    <div class="contact">
      <div class="contact-name">Ludovic Entrasse</div>
      <div class="contact-role">President / Ceo</div>
      <div class="contact-phone">519.604.3087</div>
    </div>
    <div class="footer-band">
      <div class="band-brown"></div>
      <div class="band-grey"></div>
    </div>
  </section>
</body>
</html>
```